Business card for builder specialising in renovations.

Need a card for our building business. Business name is under Martin Powles.
Have licence number on card ( 527691K)
Contact number (0400 382 415)
Want to work on logo for some business cards and shirts - something with MP or MPB or open to ideas??
No animations, No hammers. Something sharp and eye catching.
Highlight that we are a renovation specialist. Simple on front with extra details on back with some lines to jot down things.

Target Market(s)

Renovators

Industry/Entity Type

Building

Contact Information for Business Card

2 sided with room on back to jot things down.
Extra details on back so front can be simple ..like, renovations, bathrooms, decks, extensions, new builds,

Logo Text

MP

Font styles to use
Serif

Requirements
Must have
• Eye catching design .
• Name : Martin powles
• Licence number
• Contact number - 0400382415
Nice to have
• Some logo design that we can carry through to other forms of advertising
• Local builder
• Quality work
Should not have
• No animations

```html
<!DOCTYPE html>
<html lang="en">
<head>
<meta charset="utf-8">
<title>Martin Powles – Business Card</title>
<link rel="stylesheet" href="https://fonts.googleapis.com/css2?family=Gelasio:wght@400;500&display=swap">
<style>
  :root {
    --bg: #2e2e2e;
    --ink: #000000;
    --paper: #ffffff;
    --brand-blue: #27a6e0;
    --muted: #e6e6e6;
  }
  * { box-sizing: border-box; margin: 0; padding: 0; }
  html, body { width: 1200px; height: 900px; overflow: hidden; }
  body {
    background: var(--bg);
    font-family: "Gelasio", Georgia, serif;
    position: relative;
  }
  .card {
    position: absolute;
    width: 620px;
    height: 354px;
    overflow: hidden;
    box-shadow: 0 12px 30px rgba(0,0,0,.55);
  }

  /* Front */
  .card-front { left: 110px; top: 80px; background: var(--ink); border: 1px solid var(--brand-blue); }
  .front-mark {
    position: absolute; left: 50%; top: 62px; transform: translateX(-50%);
    display: flex; flex-direction: column; align-items: center;
  }
  .brand-square { width: 168px; height: 150px; background: var(--brand-blue); border: 2px solid var(--paper); }
  .front-name {
    color: var(--paper); font-size: 25px; letter-spacing: .5px; margin-top: 6px; line-height: 1;
  }
  .front-web { color: var(--paper); font-size: 15px; margin-top: 4px; }
  .front-web .accent { color: var(--brand-blue); }
  .service-bar {
    position: absolute; left: 24px; right: 24px; bottom: 26px; height: 34px;
    border: 2px solid var(--brand-blue);
    display: flex; align-items: center; justify-content: space-evenly;
    color: var(--paper); font-size: 15px; letter-spacing: .3px; text-transform: uppercase;
  }
  .service-bar .sep { width: 8px; height: 8px; background: var(--brand-blue); }

  /* Back */
  .card-back { left: 470px; top: 466px; background: var(--ink); border: 1px solid var(--brand-blue); }
  .back-white {
    position: absolute; left: 0; top: 0; bottom: 0; width: 330px; background: var(--paper);
  }
  .back-pointer { position: absolute; left: 330px; top: 80px; }
  .back-mark {
    position: absolute; left: 48px; top: 78px; width: 240px;
    display: flex; flex-direction: column; align-items: center;
  }
  .back-mark .brand-square { width: 210px; height: 168px; border: 2px solid var(--ink); }
  .back-name { color: var(--ink); font-size: 25px; margin-top: 6px; line-height: 1; letter-spacing: .5px; }
  .contact {
    position: absolute; left: 362px; top: 82px; color: var(--paper); font-size: 15px; line-height: 1.45;
  }
  .contact-name { color: var(--brand-blue); font-size: 23px; line-height: 1.1; text-transform: uppercase; }
  .contact-role { font-size: 14px; }
  .contact .label { color: var(--brand-blue); }
  .contact-line { display: flex; align-items: center; gap: 8px; }
  .contact-line svg { flex: none; }
</style>
</head>
<body>

<section class="card card-front" aria-label="Business card front">
  <div class="front-mark">
    <div class="brand-square"></div>
    <div class="front-name">MARTIN POWLES</div>
    <div class="front-web">www.<span class="accent">martinpowles</span>.com</div>
  </div>
  <div class="service-bar">
    <span>Renovations</span><span class="sep"></span>
    <span>Bathrooms Decks</span><span class="sep"></span>
    <span>Extensions</span><span class="sep"></span>
    <span>New Builds</span>
  </div>
</section>

<section class="card card-back" aria-label="Business card back">
  <div class="back-white"></div>
  <svg class="back-pointer" width="22" height="40" viewBox="0 0 22 40" aria-hidden="true">
    <polygon points="0,0 22,0 22,40" fill="#000"/>
  </svg>
  <div class="back-mark">
    <div class="brand-square"></div>
    <div class="back-name">MARTIN POWLES</div>
  </div>
  <div class="contact">
    <div class="contact-name">Martin Powles</div>
    <div class="contact-role">Director</div>
    <div><span class="label">Licence:</span> (527691K)</div>
    <div class="contact-line">
      <svg width="12" height="12" viewBox="0 0 24 24" aria-hidden="true"><path fill="#27a6e0" d="M6.6 10.8a15.1 15.1 0 0 0 6.6 6.6l2.2-2.2c.3-.3.7-.4 1-.2 1.1.4 2.3.6 3.6.6.6 0 1 .4 1 1V20c0 .6-.4 1-1 1A17 17 0 0 1 3 4c0-.6.4-1 1-1h3.5c.6 0 1 .4 1 1 0 1.3.2 2.5.6 3.6.1.3 0 .7-.2 1z"/></svg>
      <span>0400382415</span>
    </div>
    <div class="contact-line">
      <svg width="12" height="12" viewBox="0 0 24 24" aria-hidden="true"><rect x="2" y="5" width="20" height="14" fill="none" stroke="#27a6e0" stroke-width="2"/><path d="M2 5l10 8 10-8" fill="none" stroke="#27a6e0" stroke-width="2"/></svg>
      <span>info@martinpowles.com</span>
    </div>
    <div class="contact-line">
      <svg width="12" height="12" viewBox="0 0 24 24" aria-hidden="true"><circle cx="12" cy="12" r="10" fill="none" stroke="#27a6e0" stroke-width="2"/><path d="M2 12h20M12 2c3 3 3 17 0 20M12 2c-3 3-3 17 0 20" fill="none" stroke="#27a6e0" stroke-width="2"/></svg>
      <span>www.<span class="label">martinpowles</span>.com</span>
    </div>
  </div>
</section>

</body>
</html>
```